Design a New Business Card for Our Company

We are looking for fresh, unique, and a modern business card that reflects our roots as digital marketing agency focused on SEM.

Industry/Entity Type

Marketing

Contact Information for Business Card

looking for very unique out of the box designs. clean and modern that compliments our logo

Requirements
Must have
• colors should match our logo
• Front should have name, address, email, and phone/fax of the person, phone/fax are the same number
• back should have our url

```html
<!DOCTYPE html>
<html lang="en">
<head>
<meta charset="utf-8">
<title>Tidemark Solutions – Business Card</title>
<link rel="stylesheet" href="https://fonts.googleapis.com/css2?family=Open+Sans:wght@400;600;700&display=swap">
<style>
  :root {
    --page-bg: #ecebe8;
    --card-bg: #58595b;
    --brand-blue: #4f8fd0;
    --soft-grey: #b3b5b8;
    --ink-light: #ffffff;
    --card-shadow: rgba(0, 0, 0, 0.18);
  }

  * { box-sizing: border-box; margin: 0; padding: 0; }

  html, body {
    width: 1200px;
    height: 935px;
    overflow: hidden;
    background: var(--page-bg);
    font-family: "Open Sans", Arial, sans-serif;
  }

  .sheet {
    width: 1200px;
    height: 935px;
    display: flex;
    align-items: center;
    justify-content: center;
    gap: 40px;
  }

  .card {
    position: relative;
    width: 540px;
    height: 309px;
    background: var(--card-bg);
    box-shadow: 0 6px 18px var(--card-shadow);
    color: var(--ink-light);
  }

  /* ---------- Front ---------- */
  .card-front .website {
    position: absolute;
    left: 26px;
    top: 26px;
    font-size: 12px;
    color: var(--brand-blue);
    letter-spacing: 0.2px;
  }

  .card-front .brand {
    position: absolute;
    right: 26px;
    top: 20px;
    display: flex;
    align-items: center;
    gap: 10px;
  }

  .brand-dot {
    width: 14px;
    height: 14px;
    border-radius: 50%;
    background: var(--brand-blue);
  }

  .brand-name {
    font-weight: 700;
    font-size: 24px;
    color: var(--ink-light);
    letter-spacing: -0.3px;
  }

  .card-front .holder {
    position: absolute;
    right: 26px;
    top: 150px;
    text-align: right;
  }

  .holder-name {
    font-weight: 700;
    font-size: 15px;
    color: var(--brand-blue);
  }

  .holder-role {
    font-size: 12px;
    color: var(--soft-grey);
    margin-top: 2px;
  }

  .card-front .contact {
    position: absolute;
    left: 26px;
    bottom: 24px;
    list-style: none;
    font-size: 12px;
    line-height: 1.6;
    color: var(--ink-light);
  }

  .contact-label {
    font-weight: 700;
    color: var(--brand-blue);
  }

  /* ---------- Back ---------- */
  .card-back .brand {
    position: absolute;
    right: 30px;
    bottom: 56px;
    display: flex;
    align-items: center;
    gap: 12px;
  }

  .card-back .brand-name { font-size: 34px; }
  .card-back .brand-dot { width: 18px; height: 18px; }

  .card-back .website {
    position: absolute;
    right: 30px;
    bottom: 30px;
    font-size: 13px;
    color: var(--ink-light);
  }
</style>
</head>
<body>
  <main class="sheet">

    <section class="card card-front" aria-label="Business card front">
      <p class="website">www.tidemarkgroup.com</p>

      <div class="brand">
        <span class="brand-dot"></span>
        <span class="brand-name">Tidemark Solutions</span>
      </div>

      <div class="holder">
        <p class="holder-name">Owen Calder</p>
        <p class="holder-role">Owner</p>
      </div>

      <ul class="contact">
        <li><span class="contact-label">TEL</span> : 555.010.2030</li>
        <li><span class="contact-label">FAX</span> : 555.010.2030</li>
        <li>info@tidemarkgroup.com</li>
        <li>12 Alder Lane, Suite 200, Riverton, WA 00000</li>
      </ul>
    </section>

    <section class="card card-back" aria-label="Business card back">
      <div class="brand">
        <span class="brand-dot"></span>
        <span class="brand-name">Tidemark Solutions</span>
      </div>
      <p class="website">www.tidemarkgroup.com</p>
    </section>

  </main>
</body>
</html>
```